The logo name is "Harbor Skin". The name of the product will be "Cutaneous Comfort". This product is specifically formulated for amputees. Therefore under the product name it should state "for amputees". The catch phrase will be "Experience Harbor find Calmness"
These are the things we need on the label:
Logo, product name, "for amputees", "Experience Harbor find Calmness", Safe, Effective, Directions: spray on problem areas, no need to dry off. harborskin.example, Made in Canada, 500ml.
The MOST IMPORTANT and therefore the most prominent thing on this lable will be the LOGO! The second most prominent thing will be the word "Comfort" We want to keep it very plain, very simple, very unclutered. Keep in mind that this lable will be placed on a white bottle or have a white back ground. The 500ml white PE bottle with trigger sprayer will have a tear drop label. See attached die line (S-294).
We want to stay with the colours that goes with the colour scheme of the logo. See attached logo. Soft colours. We do not want a picture! We would like the lable to be classy and rich.
Updates
The logo name is "Harbor Skin". The name of the product will be "Cutaneous Comfort". This product is specificlly formulated for amputees. Therefore under the product name it should state "for amputees". The catch phrase will be "Experience Harbor find Calmness"
Logo, product name, "for amputees", catch phrase "Experience Harbor find Calmness", Clean, Safe, Effective, Directions: spray on problem areas, no need to dry off. Also Harbor Skin Corpation, harborskin.example, Made in Canada, 500ml.
We want to stay with the colour scheme of the logo. See attached logo. Soft colours. We do not want a picture! We would like the lable to be classy and rich.
This is the offical directive that came from the governing panal of this lable. This panal it not know where it wanted to take this lable that would represent this line until they review all of your submissions, thank you for all your talented hard work. But now it is clear it is time to regroup and hit this objective.
Project Deadline Extended
Reason: New restrictions on lable wording for this product.
Target Market(s)
Amputees and Parents of.
Industry/Entity Type
Product
Requirements
Must have
- Final product to be in a pdf or an illustrator file

```html
<!DOCTYPE html>
<html lang="en">
<head>
<meta charset="utf-8">
<title>Harbor Skin – Cutaneous Comfort Label</title>
<link rel="stylesheet" href="https://fonts.googleapis.com/css2?family=Libre+Baskerville:wght@700&family=Oswald:wght@600&family=Kalam:wght@400&family=Open+Sans:wght@400;700&display=swap">
<style>
  :root{
    --stage:#dcdcdc;
    --label:#ffffff;
    --green:#1f7f66;
    --green-dark:#135a48;
    --teal:#27b8b0;
    --gold:#f6c46a;
    --orange:#f3b24a;
    --ink:#1d1d1d;
    --logo-green:#1e6b4f;
  }
  *{margin:0;padding:0;box-sizing:border-box}
  html,body{width:1200px;height:1000px;overflow:hidden}
  body{background:var(--stage);position:relative;font-family:"Open Sans",Arial,sans-serif;color:var(--ink)}
  .label-shape{position:absolute;left:0;top:0}
  .label{position:absolute;left:0;top:0;width:1200px;height:1000px}
  .brand{position:absolute;left:492px;top:548px;display:flex;align-items:center;gap:10px}
  .brand-mark{width:34px;height:34px;background:var(--teal)}
  .brand-name{font-family:"Libre Baskerville",Georgia,serif;font-weight:700;font-size:28px;color:var(--logo-green);letter-spacing:-0.5px}
  .gold-rule{position:absolute;left:430px;top:618px;width:276px;height:6px;background:var(--gold)}
  .subname{position:absolute;left:522px;top:620px;width:132px;height:22px;background:var(--gold);
    font-family:"Kalam",cursive;font-size:19px;line-height:22px;color:var(--label);text-align:center;letter-spacing:1px}
  .band{position:absolute;left:460px;top:642px;width:286px;height:80px;
    background:linear-gradient(90deg,rgba(31,127,102,0) 0%,var(--green) 12%,var(--green) 88%,rgba(31,127,102,0) 100%)}
  .band::after{content:"";position:absolute;left:0;right:0;bottom:-6px;height:6px;
    background:linear-gradient(90deg,rgba(39,184,176,0),rgba(39,184,176,.5) 20%,rgba(39,184,176,.5) 80%,rgba(39,184,176,0))}
  .product{position:absolute;left:460px;top:642px;width:286px;text-align:center;
    font-family:"Oswald",Impact,sans-serif;font-weight:600;font-size:60px;line-height:80px;letter-spacing:3px;
    color:var(--label);-webkit-text-stroke:2px var(--green-dark)}
  .audience{position:absolute;left:526px;top:726px;width:130px;height:46px;background:var(--teal);
    color:var(--label);text-align:center}
  .audience-for{display:block;font-family:"Kalam",cursive;font-size:18px;line-height:20px}
  .audience-who{display:block;font-weight:700;font-style:italic;font-size:18px;line-height:22px;letter-spacing:.5px}
  .tagline{position:absolute;left:430px;top:785px;width:340px;text-align:center;
    font-weight:700;font-size:16px;color:var(--orange)}
  .claims{position:absolute;left:510px;top:812px;width:160px;height:15px;border-radius:8px;background:var(--teal);
    color:var(--label);font-size:10px;font-weight:700;font-style:italic;text-align:center;line-height:15px;letter-spacing:1px}
  .info{position:absolute;left:430px;top:838px;width:340px;text-align:center;font-size:9px;line-height:11px}
  .info strong{font-weight:700}
  .info .gap{display:block;height:3px}
  .web{font-weight:700;font-size:10px}
  .origin{font-size:7px}
  .volume{display:inline-block;margin-top:4px;padding:0 7px;border-radius:7px;background:var(--green-dark);
    color:var(--label);font-size:8px;font-weight:700;line-height:13px}
</style>
</head>
<body>
  <svg class="label-shape" width="1200" height="1000" viewBox="0 0 1200 1000" aria-hidden="true">
    <path d="M712 352 C742 346 762 382 768 424 L772 880 Q772 936 712 936 L490 936 Q428 936 428 880 L428 640 Q428 604 458 576 Z"
          fill="#ffffff" stroke="#c9c9c9" stroke-width="1"/>
  </svg>

  <div class="label">
    <div class="brand">
      <span class="brand-mark"></span>
      <span class="brand-name">Harbor Skin</span>
    </div>

    <div class="gold-rule"></div>
    <div class="subname">Cutaneous</div>
    <div class="band"></div>
    <div class="product">COMFORT</div>

    <div class="audience">
      <span class="audience-for">For</span>
      <span class="audience-who">AMPUTEES</span>
    </div>

    <p class="tagline">Experience Harbor Find Calmness</p>
    <div class="claims">CLEAN, SAFE &amp; EFFECTIVE</div>

    <div class="info">
      <strong>Directions:</strong><br>
      Spray on problem areas, no need to dry off.
      <span class="gap"></span>
      <strong>Manufactured by:</strong><br>
      Harbor Skin Corpation
      <span class="gap"></span>
      <span class="web">www.harborskin.example</span>
      <span class="gap"></span>
      <span class="origin">Made in Canada</span><br>
      <span class="volume">500mL</span>
    </div>
  </div>
</body>
</html>
```